Moonridge Real Estate Sign

We are in the process of rebranding our business and need a new For Sale \ Sold sign.
We're a prestige real estate agency and therefore require a really stylish sign.
I've uploaded the following files
1. The new company logo
2. "sample sign.jpg" which shows the type of sign we would like. It is a metal sign with a top panel and bottom panel.
3. Our previous sign "previous sign.jpg" if you're interested in seeing it.
The sign must be black with white text.
Our thoughts are that the top panel (refer to sample sign) would contain the text "For Sale" or "Sold". These would be two separate panels which are interchangeable and could be screwed in place.
The bottom panel would not contain any photos like the sample. However, it may contain our logo and my contact details etc.
The sign is 900mm wide x 1200mm high.
My details are:
Name: Gerald Fenwick
Web: www.mrrealestate.com.au
Email: sales@mrrealestate.com.au
Phone: 0491 806 357

```html
<!DOCTYPE html>
<html lang="en">
<head>
<meta charset="utf-8">
<title>Moonridge Real Estate – For Sale Sign</title>
<link rel="stylesheet" href="https://fonts.googleapis.com/css2?family=Montserrat:wght@400;500;600;700&display=swap">
<style>
  :root {
    --ink: #111111;
    --paper: #ffffff;
    --backdrop: #eceeef;
    --skyline: #dcdcdc;
    --skyline-dark: #cfcfcf;
    --info-grey: #c8c8c8;
    --text-dark: #1a1a1a;
  }
  * { margin: 0; padding: 0; box-sizing: border-box; }
  html, body {
    width: 1019px;
    height: 1200px;
    overflow: hidden;
    background: var(--backdrop);
    font-family: "Montserrat", sans-serif;
  }
  .sign {
    position: absolute;
    left: 60px;
    top: 275px;
    width: 900px;
    height: 650px;
    background: var(--ink);
    padding: 0 18px 18px 18px;
  }
  .sign__header {
    height: 190px;
    display: flex;
    align-items: center;
    justify-content: center;
    color: var(--paper);
    font-weight: 600;
    font-size: 112px;
    letter-spacing: 6px;
  }
  .sign__body {
    height: 442px;
    background: var(--paper);
    padding: 22px 26px 22px 26px;
    display: flex;
    flex-direction: column;
  }
  .brand {
    position: relative;
    height: 160px;
  }
  .brand__skyline {
    position: absolute;
    inset: 0;
    background: linear-gradient(180deg, var(--skyline) 0%, var(--skyline-dark) 100%);
  }
  .brand__lockup {
    position: relative;
    height: 100%;
    display: flex;
    align-items: center;
    justify-content: center;
    gap: 26px;
    padding-top: 10px;
  }
  .brand__mark {
    width: 88px;
    height: 88px;
    background: var(--text-dark);
  }
  .brand__name {
    color: var(--text-dark);
    font-weight: 700;
    font-size: 58px;
    line-height: 1;
  }
  .brand__tagline {
    display: block;
    font-size: 30px;
    letter-spacing: 8px;
    margin-top: 6px;
    text-align: right;
  }
  .agent {
    margin-top: 6px;
    height: 42px;
    background: var(--ink);
    color: var(--paper);
    font-weight: 600;
    font-size: 32px;
    display: flex;
    align-items: center;
    justify-content: center;
    letter-spacing: 1px;
  }
  .contact {
    margin-top: 8px;
    flex: 1;
    background: var(--info-grey);
    color: var(--text-dark);
    text-align: center;
    display: flex;
    flex-direction: column;
    justify-content: center;
  }
  .contact__phone {
    font-weight: 700;
    font-size: 74px;
    line-height: 1;
  }
  .contact__email {
    margin-top: 20px;
    font-size: 19px;
    letter-spacing: 2px;
  }
  .contact__web {
    margin-top: 4px;
    font-weight: 700;
    font-size: 25px;
    letter-spacing: 1px;
  }
</style>
</head>
<body>
  <div class="sign">
    <div class="sign__header">FOR SALE</div>
    <div class="sign__body">
      <div class="brand">
        <div class="brand__skyline" role="img" aria-label="Soft grey city skyline silhouette behind the logo"></div>
        <div class="brand__lockup">
          <div class="brand__mark"></div>
          <div class="brand__name">Moonridge<span class="brand__tagline">REAL ESTATE</span></div>
        </div>
      </div>
      <div class="agent">Gerald Fenwick</div>
      <div class="contact">
        <div class="contact__phone">Ph:0491 806 357</div>
        <div class="contact__email">Email: sales@mrrealestate.com.au</div>
        <div class="contact__web">www.mrrealestate.com.au</div>
      </div>
    </div>
  </div>
</body>
</html>
```